Soho based IT support firm flyer.

We need a flyer to boost our business. We're a tech support firm based in Soho, London and provide helpdesk and call out support to SMEs in and around London.
They'll be two flyers with the same design. One is location specific and has the copy:
-
1 Month Free IT Support!
Based in Soho, we provide expert tech support for both Novabooks and PCs.
We have monthly as well as pay-as-you-go plans to fit your business.
Call us now and we'll show you how we can save you up to 50% on your IT spend.
-None location based is-
1 Month Free IT Support!
We provide expert, professional tech support for both Novabooks and PCs.
• Dedicated full time helpdesk
• Same day onsite visits
• Proactive support with monitoring
• 98% satisfaction score*
*taken from satisfaction survey sent out on closure of every case for Oct 2011 to Oct 2012
-
The location one needs to include a map with our location marked as postcode K7R 4TB.
I'm fine with royalty photos being used within a reasonable price. Please use Pixmarrow.
Our site shows our brand best. Please keep as close to this as possible.
http://quillnet-hub.example
Thanks for looking.

```html
<!DOCTYPE html>
<html lang="en">
<head>
<meta charset="utf-8">
<title>Quillnet IT Support Flyer</title>
<link rel="stylesheet" href="https://fonts.googleapis.com/css2?family=Arimo:wght@400;700&family=Roboto+Condensed:wght@400;700&display=swap">
<style>
  :root {
    --lime: #a8cf3a;
    --lime-dark: #8fb52a;
    --charcoal: #3b3c3e;
    --ink: #1d1d1d;
    --white: #ffffff;
    --orange: #f39a1e;
    --muted: #c9c9c9;
    --photo-a: #1f3f66;
    --photo-b: #8fb4d8;
  }
  * { box-sizing: border-box; margin: 0; padding: 0; }
  html, body { width: 849px; height: 1200px; overflow: hidden; background: var(--white); }
  body { font-family: "Arimo", Arial, sans-serif; }
  .flyer { position: relative; width: 849px; height: 1200px; overflow: hidden; background: var(--charcoal); }

  .headline-band {
    position: absolute; left: 0; top: 0; width: 849px; height: 178px;
    background: var(--lime);
    display: flex; align-items: center; justify-content: center;
  }
  .headline {
    font-weight: 700; font-size: 50px; line-height: 1.1; color: var(--ink);
    text-align: center; letter-spacing: -0.5px;
  }

  .hero-photo {
    position: absolute; left: 0; top: 178px; width: 849px; height: 500px;
    background: linear-gradient(120deg, var(--photo-a) 0%, #3d6c9c 40%, var(--photo-b) 75%, #dfe9f2 100%);
  }

  .panel-shape { position: absolute; left: 0; top: 540px; width: 849px; height: 600px; }

  .brand {
    position: absolute; left: 62px; top: 592px;
    display: flex; align-items: center; gap: 14px;
    font-weight: 700; font-size: 58px; color: var(--lime-dark); letter-spacing: -1px;
  }
  .brand-dot { width: 22px; height: 22px; border-radius: 50%; background: var(--lime); }

  .offer-badge {
    position: absolute; left: 628px; top: 483px; width: 205px; height: 205px;
    border-radius: 50%; background: var(--orange); border: 6px solid var(--white);
    display: flex; flex-direction: column; align-items: center; justify-content: center;
    color: var(--white); text-align: center; font-weight: 700;
  }
  .offer-badge .free { font-size: 54px; line-height: 1; }
  .offer-badge .detail { font-size: 25px; line-height: 1.1; margin-top: 4px; }

  .benefits { position: absolute; top: 716px; list-style: none; font-family: "Roboto Condensed", "Arial Narrow", sans-serif; }
  .benefits.left { left: 26px; width: 400px; }
  .benefits.right { left: 477px; width: 360px; }
  .benefits li {
    position: relative; padding-left: 40px; margin-bottom: 10px;
    color: var(--lime); font-weight: 700; font-size: 30px; line-height: 32px;
  }
  .benefits.right li { margin-bottom: 16px; }
  .benefits li::before {
    content: ""; position: absolute; left: 6px; top: 7px;
    width: 16px; height: 16px; border: 4px solid var(--white); border-radius: 50%;
  }
  .footnote { display: block; margin-top: 4px; font-weight: 400; font-size: 17px; line-height: 20px; color: var(--muted); }

  .contact-band {
    position: absolute; left: 0; top: 1128px; width: 849px; height: 72px;
    background: var(--lime); display: flex; align-items: center; padding: 0 30px;
  }
  .phone { display: flex; align-items: center; gap: 16px; font-weight: 700; font-size: 46px; color: var(--white); }
  .phone svg { width: 40px; height: 40px; }
  .contact-links { margin-left: auto; list-style: none; }
  .contact-links li {
    display: flex; align-items: center; gap: 10px;
    font-weight: 700; font-size: 20px; line-height: 1.35; color: var(--ink);
  }
  .contact-links li::before { content: ""; width: 13px; height: 13px; background: var(--white); }
</style>
</head>
<body>
<div class="flyer">
  <header class="headline-band">
    <h1 class="headline">A one stop shop for all of<br>your business’ IT needs</h1>
  </header>

  <div class="hero-photo" role="img" aria-label="Photo of a support technician at a desk holding a magnifying glass in front of a blue world map"></div>

  <svg class="panel-shape" viewBox="0 0 849 600" preserveAspectRatio="none" aria-hidden="true">
    <path d="M0 20 C 180 20, 300 50, 420 110 C 560 170, 700 110, 849 60 L 849 600 L 0 600 Z" fill="#ffffff"/>
    <path d="M0 160 C 200 165, 330 150, 450 140 C 600 125, 720 100, 849 85 L 849 600 L 0 600 Z" fill="#3b3c3e"/>
  </svg>

  <div class="brand"><span>Quillnet</span><span class="brand-dot"></span></div>

  <div class="offer-badge">
    <span class="free">FREE</span>
    <span class="detail">One Month<br>IT Support!</span>
  </div>

  <ul class="benefits left">
    <li>We provide expert, professional tech support for both Novabooks and PCs.</li>
    <li>We have monthly as well as pay-as-you-go plans to fit your business.</li>
    <li>Call us now and we’ll show you how we can save you up to 50% on your IT spend.</li>
  </ul>

  <ul class="benefits right">
    <li>Dedicated full time helpdesk</li>
    <li>Same day onsite visits</li>
    <li>Proactive support with monitoring</li>
    <li>98% satisfaction score*
      <span class="footnote">taken from satisfaction survey sent out on closure of every case for Oct 2011 to Oct 2012</span>
    </li>
  </ul>

  <footer class="contact-band">
    <div class="phone">
      <svg viewBox="0 0 24 24" aria-hidden="true"><path fill="#ffffff" d="M6.6 10.8a15.1 15.1 0 0 0 6.6 6.6l2.2-2.2a1 1 0 0 1 1-.25 11.4 11.4 0 0 0 3.6.57 1 1 0 0 1 1 1V20a1 1 0 0 1-1 1A17 17 0 0 1 3 4a1 1 0 0 1 1-1h3.5a1 1 0 0 1 1 1c0 1.25.2 2.45.57 3.57a1 1 0 0 1-.25 1z"/></svg>
      <span>0203 555 0148</span>
    </div>
    <ul class="contact-links">
      <li>info@quillnet-hub.example</li>
      <li>www.quillnet-hub.example</li>
    </ul>
  </footer>
</div>
</body>
</html>
```